Business Cards for new orthopaedic surgery practice

My husband and I are starting our own orthopaedic surgery practice. We are looking for a business card that is uniform, but one will have my name/title and the other will have his. You can just create one design with my name on it for now. But when I choose your design as the winning design I will ask that you add another copy with his name/title.

We are looking for classy, simple, elite all in one. We like dark blues/a little gold/yellow. Something that goes with our logo. We want our logo incorporated. Here is all the info you need:
Business name: RV Bone & Vitality Center
Location: 38517 North Willowmere Ave
Palm Hollow, FL 33990
Phone: 954-218-4063
Fax: 954-582-7341
Email: info@myrvbonecare.example

Names: Lydia Vance, M.D.
Board Certified Hand and Upper Extremity Surgeon

Ebo Dansu, M.D.
Board Certified Hip & Knee Replacement/General Orthopaedic Surgeon

Can decide what you want to put on the back. Maybe a slogan:
Rooted in Care. Focused on You

I am just going to upload our logo. The only thing is if we select you as the winning design, the location, and phone numbers may change. We will need your help to update that once fully solidified.

Industry/Entity Type

Medical

Contact Information for Business Card

Colors
0054AA
0677BA
7BADD7
CADEEF
E8F1F8
0094D4
00A9DD
6FCCEA
C7EBF8
E9F6FB

Requirements
Must have
• class, appeal,
Should not have
• We want to air on the side of masculine if we are looking at masculine vs. feminine feel. But we still want it classy, sophisticated, and something we will love

```html
<!DOCTYPE html>
<html lang="en">
<head>
<meta charset="UTF-8">
<title>RV Bone &amp; Vitality Center – Business Card</title>
<link href="https://fonts.googleapis.com/css2?family=Montserrat:wght@400;500;600&display=swap" rel="stylesheet">
<style>
  :root {
    --navy: #1c2a52;
    --navy-soft: #2b3a66;
    --gold: #c9a15a;
    --ink: #1d1d1f;
    --paper: #ffffff;
    --backdrop: #e4e5e8;
  }
  * { box-sizing: border-box; margin: 0; padding: 0; }
  html, body { width: 1200px; height: 1200px; overflow: hidden; }
  body {
    background: var(--backdrop);
    font-family: "Montserrat", sans-serif;
    position: relative;
  }
  .card {
    position: absolute;
    left: 150px;
    width: 900px;
    height: 514px;
    border-radius: 40px;
    overflow: hidden;
    box-shadow: 0 10px 30px rgba(0,0,0,0.18);
  }
  .card--front { top: 60px; background: var(--paper); }
  .card--back  { top: 626px; background: var(--navy); border-bottom: 4px solid var(--gold); }

  .identity {
    position: absolute;
    left: 70px;
    top: 150px;
    color: var(--ink);
  }
  .identity__name {
    color: var(--gold);
    font-weight: 600;
    font-size: 30px;
    letter-spacing: 0.5px;
    text-transform: uppercase;
  }
  .identity__title {
    font-size: 19px;
    line-height: 1.15;
    margin-top: 4px;
  }
  .contact {
    list-style: none;
    margin-top: 26px;
    font-size: 19px;
    line-height: 1.2;
  }
  .contact li { display: flex; align-items: flex-start; gap: 14px; margin-bottom: 6px; }
  .contact svg { width: 22px; height: 22px; flex: none; margin-top: 1px; fill: var(--gold); }

  .mark {
    position: absolute;
    left: 530px;
    top: 60px;
    width: 300px;
    height: 300px;
  }
  .mark svg { position: absolute; inset: 0; }
  .mark__name {
    position: absolute;
    inset: 0;
    display: flex;
    align-items: center;
    justify-content: center;
    text-align: center;
    font-weight: 600;
    font-size: 26px;
    line-height: 1.25;
    letter-spacing: 1px;
    text-transform: uppercase;
    color: var(--navy);
  }
  .band { position: absolute; left: 0; bottom: 0; width: 900px; height: 40px; }

  .card--back .mark { left: 280px; top: 87px; width: 340px; height: 340px; }
  .card--back .mark__name { color: var(--navy-soft); font-size: 30px; }
</style>
</head>
<body>

<section class="card card--front" aria-label="Business card front">
  <div class="identity">
    <h1 class="identity__name">Lydia Vance, M.D.</h1>
    <p class="identity__title">Board Certified Hand and<br>Upper Extremity Surgeon</p>
    <ul class="contact">
      <li>
        <svg viewBox="0 0 24 24" aria-hidden="true"><path d="M6.6 10.8a15.1 15.1 0 0 0 6.6 6.6l2.2-2.2a1 1 0 0 1 1-.25 11.4 11.4 0 0 0 3.6.57 1 1 0 0 1 1 1V20a1 1 0 0 1-1 1A17 17 0 0 1 3 4a1 1 0 0 1 1-1h3.5a1 1 0 0 1 1 1c0 1.25.2 2.45.57 3.57a1 1 0 0 1-.25 1z"/></svg>
        954-218-4063
      </li>
      <li>
        <svg viewBox="0 0 24 24" aria-hidden="true"><path d="M7 2h8l3 3v5H7zM4 10h16a2 2 0 0 1 2 2v8a2 2 0 0 1-2 2H4a2 2 0 0 1-2-2v-8a2 2 0 0 1 2-2zm3 4v2h2v-2zm4 0v2h2v-2zm4 0v2h2v-2zm-8 4v2h2v-2zm4 0v2h2v-2zm4 0v2h2v-2z"/></svg>
        954-582-7341
      </li>
      <li>
        <svg viewBox="0 0 24 24" aria-hidden="true"><path d="M2 5h20v14H2zm2 2v.5l8 5.5 8-5.5V7zm0 3v7h16v-7l-8 5.5z"/></svg>
        info@myrvbonecare.example
      </li>
      <li>
        <svg viewBox="0 0 24 24" aria-hidden="true"><path d="M12 2a7 7 0 0 0-7 7c0 5.2 7 13 7 13s7-7.8 7-13a7 7 0 0 0-7-7zm0 9.5A2.5 2.5 0 1 1 12 6.5a2.5 2.5 0 0 1 0 5z"/></svg>
        <span>38517 North Willowmere Ave<br>Palm Hollow, FL 33990</span>
      </li>
    </ul>
  </div>

  <div class="mark">
    <svg viewBox="0 0 300 300" aria-hidden="true">
      <path d="M60 230 A110 110 0 0 1 60 70" fill="none" stroke="var(--gold)" stroke-width="2.5"/>
      <path d="M240 70 A110 110 0 0 1 240 230" fill="none" stroke="var(--gold)" stroke-width="2.5"/>
    </svg>
    <p class="mark__name">RV Bone &amp;<br>Vitality<br>Center</p>
  </div>

  <svg class="band" viewBox="0 0 900 40" preserveAspectRatio="none" aria-hidden="true">
    <polygon points="0,22 580,22 568,40 0,40" fill="var(--gold)"/>
    <polygon points="592,14 900,4 900,40 580,40" fill="var(--navy)"/>
  </svg>
</section>

<section class="card card--back" aria-label="Business card back">
  <div class="mark">
    <svg viewBox="0 0 340 340" aria-hidden="true">
      <path d="M65 265 A125 125 0 0 1 65 75" fill="none" stroke="var(--navy-soft)" stroke-width="3"/>
      <path d="M275 75 A125 125 0 0 1 275 265" fill="none" stroke="var(--navy-soft)" stroke-width="3"/>
    </svg>
    <p class="mark__name">RV Bone &amp;<br>Vitality<br>Center</p>
  </div>
</section>

</body>
</html>
```